Business card for medical clinic

I need an upmarket, modern medical/health business card for my clinic

Contact Information for Business Card

name, address, email, qr code

```html
<!DOCTYPE html>
<html lang="en">
<head>
<meta charset="utf-8">
<title>Corvena Health Partners – Business Card</title>
<link rel="stylesheet" href="https://fonts.googleapis.com/css2?family=Montserrat:wght@400;500;700&display=swap">
<style>
  :root {
    --backdrop: #c9c9cb;
    --navy: #1f2b48;
    --deep-blue: #27496b;
    --sky: #29a9e1;
    --sky-light: #2fb0e6;
    --white: #ffffff;
    --silver: #d9dadc;
    --shadow: rgba(0, 0, 0, 0.28);
  }
  * { box-sizing: border-box; margin: 0; padding: 0; }
  html, body {
    width: 1200px; height: 813px; overflow: hidden;
    background: var(--backdrop);
    font-family: "Montserrat", sans-serif;
  }
  .sheet {
    width: 1200px; height: 813px;
    display: flex; align-items: center; justify-content: center; gap: 50px;
  }
  .card {
    position: relative;
    width: 540px; height: 309px;
    border-radius: 22px;
    overflow: hidden;
    box-shadow: 0 12px 28px var(--shadow);
  }
  .card-art { position: absolute; inset: 0; width: 100%; height: 100%; }

  /* Contact side */
  .contact-list {
    position: absolute; left: 34px; top: 36px;
    color: var(--white);
  }
  .person-name {
    font-weight: 700; font-size: 25px; letter-spacing: 1px;
    text-transform: uppercase; line-height: 1;
  }
  .person-title { font-size: 13px; font-weight: 400; margin-top: 6px; }
  .contact-rows { margin-top: 22px; display: flex; flex-direction: column; gap: 13px; }
  .contact-row { display: flex; align-items: center; gap: 14px; }
  .hex-icon { width: 34px; height: 38px; flex: none; }
  .contact-text { font-size: 12.5px; line-height: 1.35; }
  .hex-chain {
    position: absolute; left: 50px; top: 118px;
    width: 2px; height: 160px; background: var(--white);
  }
  .brand-mini {
    position: absolute; right: 26px; top: 126px;
    display: flex; align-items: center; gap: 8px;
    color: var(--deep-blue);
    font-weight: 500; font-size: 15px; letter-spacing: 2px; text-transform: uppercase;
    line-height: 1.2;
  }
  .brand-dot { width: 18px; height: 18px; border-radius: 50%; border: 2px solid var(--deep-blue); flex: none; }

  /* Brand side */
  .card-front {
    background: linear-gradient(30deg, var(--sky) 0%, #2f7fae 40%, var(--deep-blue) 70%, var(--navy) 100%);
  }
  .brand-lockup {
    position: absolute; left: 0; right: 0; top: 104px;
    display: flex; align-items: center; justify-content: center; gap: 16px;
    color: var(--white);
  }
  .brand-ring { width: 40px; height: 40px; border-radius: 50%; border: 3px solid var(--white); flex: none; }
  .brand-name {
    font-weight: 500; font-size: 28px; letter-spacing: 4px; text-transform: uppercase; line-height: 1.2;
  }
  .web-line {
    position: absolute; left: 0; right: 0; bottom: 36px;
    display: flex; align-items: center; justify-content: center; gap: 8px;
    color: var(--white); font-size: 13px; letter-spacing: 0.5px;
  }
  .globe { width: 16px; height: 16px; }
</style>
</head>
<body>
<main class="sheet">

  <section class="card card-back" aria-label="Business card, contact side">
    <svg class="card-art" viewBox="0 0 540 309" aria-hidden="true">
      <defs>
        <linearGradient id="contactFill" x1="0" y1="1" x2="1" y2="0">
          <stop offset="0" stop-color="#2aa5dc"/>
          <stop offset="0.5" stop-color="#2c6b95"/>
          <stop offset="1" stop-color="#1f2b48"/>
        </linearGradient>
      </defs>
      <rect width="540" height="309" fill="url(#contactFill)"/>
      <polygon points="322,0 268,154.5 322,309 345,309 291,154.5 345,0" fill="#29a9e1"/>
      <polygon points="345,0 291,154.5 345,309 352,309 298,154.5 352,0" fill="#d9dadc"/>
      <polygon points="352,0 298,154.5 352,309 362,309 308,154.5 362,0" fill="#1f2b48"/>
      <polygon points="362,0 308,154.5 362,309 540,309 540,0" fill="#ffffff"/>
    </svg>

    <div class="hex-chain" aria-hidden="true"></div>
    <div class="contact-list">
      <h1 class="person-name">Daniel Mercer</h1>
      <p class="person-title">Managing Director</p>
      <div class="contact-rows">
        <div class="contact-row">
          <svg class="hex-icon" viewBox="0 0 34 38" aria-hidden="true">
            <polygon points="17,1 32,10 32,28 17,37 2,28 2,10" fill="#ffffff"/>
            <circle cx="17" cy="15" r="4.5" fill="#2a8fc4"/>
            <path d="M9 27 q8 -10 16 0 z" fill="#2a8fc4"/>
          </svg>
          <p class="contact-text">555-014-2270<br>555-014-2271</p>
        </div>
        <div class="contact-row">
          <svg class="hex-icon" viewBox="0 0 34 38" aria-hidden="true">
            <polygon points="17,1 32,10 32,28 17,37 2,28 2,10" fill="#2a8fc4" stroke="#ffffff" stroke-width="2.5"/>
            <path d="M10 13 h14 v3 h-3 v-1 h-8 v1 h-3 z M12 18 h10 l2 8 h-14 z" fill="#ffffff"/>
          </svg>
          <p class="contact-text">info@corvenaclinic.com<br>www.corvenaclinic.com</p>
        </div>
        <div class="contact-row">
          <svg class="hex-icon" viewBox="0 0 34 38" aria-hidden="true">
            <polygon points="17,1 32,10 32,28 17,37 2,28 2,10" fill="#2a8fc4" stroke="#ffffff" stroke-width="2.5"/>
            <path d="M9.5 20 a7.5 7.5 0 1 1 15 0 c0 5 -7.5 10 -7.5 10 s-7.5 -5 -7.5 -10 z" fill="#ffffff"/>
            <circle cx="17" cy="19.5" r="2.8" fill="#2a8fc4"/>
          </svg>
          <p class="contact-text">48 Alder Ridge Road,<br>Fairbrook, WI 53000</p>
        </div>
      </div>
    </div>

    <div class="brand-mini">
      <span class="brand-dot" aria-hidden="true"></span>
      <span>Corvena Health<br>Partners</span>
    </div>
  </section>

  <section class="card card-front" aria-label="Business card, brand side">
    <div class="brand-lockup">
      <span class="brand-ring" aria-hidden="true"></span>
      <p class="brand-name">Corvena Health<br>Partners</p>
    </div>
    <p class="web-line">
      <svg class="globe" viewBox="0 0 16 16" aria-hidden="true">
        <circle cx="8" cy="8" r="6.5" fill="none" stroke="#ffffff" stroke-width="1.3"/>
        <ellipse cx="8" cy="8" rx="3" ry="6.5" fill="none" stroke="#ffffff" stroke-width="1.1"/>
        <line x1="1.5" y1="8" x2="14.5" y2="8" stroke="#ffffff" stroke-width="1.1"/>
      </svg>
      www.corvenahealth.com
    </p>
  </section>

</main>
</body>
</html>
```